Business Card Update, need to bring life to the card, two sided color

We need a new business card design, are moving and changing addresses and need a new look, we have the logos already attached but need a new style moving forward. Can incorporate the color of the logo (The Green) as well, maybe a solid back? We deal with safety products revolving around static electricity and safety lighting. Would like to keep same font in second logo as well.

Target Market(s)

Electrical Safety, Lighting

Contact Information for Business Card

Dale Fenwick
Vice President
Office: 770-555-4821
Cell: 770-555-3067
dale@tkfenwick.example
www.tkfenwick.example
4700 West Harbor Boulevard
Suite #150
Roswell, GA 30076

Font styles to use
Serif
Sans Serif

Requirements
Must have
• Since 1918
Nice to have
• Could use the 100 Year Logo for back of card, would like the back of card to be the same green as logo.
Should not have
• No black cards please.

```html
<!DOCTYPE html>
<html lang="en">
<head>
<meta charset="utf-8">
<title>T.K. Fenwick Business Card</title>
<link rel="stylesheet" href="https://fonts.googleapis.com/css2?family=Arimo:wght@700&family=Source+Sans+3:wght@400;600&display=swap">
<style>
  :root {
    --brand-green: #00985a;
    --deep-green: #006b3f;
    --ink: #000000;
    --paper: #ffffff;
    --stage: #eef2f0;
    --frame: #2b2b2b;
    --edge: #9a9a9a;
  }
  * { margin: 0; padding: 0; box-sizing: border-box; }
  html, body { width: 1200px; height: 1007px; overflow: hidden; }
  body {
    background: var(--stage);
    border: 3px solid var(--frame);
    position: relative;
    font-family: "Source Sans 3", "Myriad Pro", sans-serif;
  }
  .card {
    position: absolute;
    background: var(--paper);
    border: 1px solid var(--edge);
    border-radius: 41px;
    overflow: hidden;
  }
  .card-front { left: 44px; top: 30px; width: 811px; height: 462px; }
  .card-back  { left: 323px; top: 504px; width: 821px; height: 470px; }
  .band { position: absolute; left: 0; top: 0; width: 100%; height: 100%; }

  .brand-mark {
    position: absolute; left: 144px; top: 30px;
    width: 130px; height: 130px; border-radius: 50%;
    background: var(--brand-green);
  }
  .company-name {
    position: absolute; left: 292px; top: 64px;
    font-family: "Arimo", Arial, sans-serif; font-weight: 700;
    font-size: 44px; line-height: 1; color: var(--brand-green);
    white-space: nowrap;
  }
  .company-sub {
    position: absolute; left: 318px; top: 110px;
    font-family: "Arimo", Arial, sans-serif; font-weight: 700;
    font-size: 20px; line-height: 1; color: var(--brand-green);
    letter-spacing: 0.3px; white-space: nowrap;
  }
  .since {
    position: absolute; left: 318px; top: 138px;
    font-size: 17px; font-weight: 600; line-height: 1;
    color: var(--deep-green); letter-spacing: 2px; white-space: nowrap;
  }
  .person {
    position: absolute; left: 0; width: 100%; top: 226px; text-align: center;
    font-family: "Arimo", Arial, sans-serif; font-weight: 700;
    white-space: nowrap; line-height: 1;
  }
  .person-name { font-size: 31px; color: var(--brand-green); }
  .person-title { font-size: 24px; color: var(--ink); }

  .contact {
    position: absolute; color: var(--paper); font-size: 19px;
    line-height: 1; white-space: nowrap; display: flex; align-items: center; gap: 6px;
  }
  .contact svg { width: 18px; height: 18px; flex: none; }
  .contact-phone { left: 0; width: 100%; justify-content: center; top: 334px; }
  .contact-line { left: 0; width: 100%; justify-content: center; top: 373px; gap: 22px; }
  .contact-line .item { display: flex; align-items: center; gap: 6px; }
  .contact-address { left: 0; width: 100%; justify-content: center; top: 416px; }

  .back-mark {
    position: absolute; left: 324px; top: 60px;
    width: 200px; height: 200px; border-radius: 50%;
    background: var(--brand-green);
  }
  .back-name {
    position: absolute; left: 0; width: 100%; top: 284px; text-align: center;
    font-family: "Arimo", Arial, sans-serif; font-weight: 700;
    font-size: 40px; line-height: 1; color: var(--brand-green);
  }
  .back-since {
    position: absolute; left: 0; width: 100%; top: 334px; text-align: center;
    font-size: 18px; font-weight: 600; line-height: 1;
    color: var(--deep-green); letter-spacing: 3px;
  }
  .back-web {
    position: absolute; left: 0; width: 100%; top: 434px;
    justify-content: center; font-size: 23px; letter-spacing: 5px;
  }
</style>
</head>
<body>

<section class="card card-front">
  <svg class="band" viewBox="0 0 811 462" preserveAspectRatio="none" aria-hidden="true">
    <path d="M0,372 Q405,218 811,372 L811,462 L0,462 Z" fill="var(--brand-green)"/>
    <path d="M0,360 Q405,204 811,368 Q405,216 0,372 Z" fill="var(--deep-green)"/>
  </svg>
  <div class="brand-mark"></div>
  <div class="company-name">T.K. Fenwick</div>
  <div class="company-sub">Manufacturing Company, Inc.</div>
  <div class="since">SINCE 1918</div>
  <div class="person"><span class="person-name">Dale Fenwick</span><span class="person-title">, Vice President</span></div>

  <div class="contact contact-phone">
    <svg viewBox="0 0 20 20"><circle cx="10" cy="10" r="8.5" fill="none" stroke="#fff" stroke-width="1.5"/><path d="M7 5.5c-1 .8-1 2.2 0 4s2.5 3.6 4.3 4.5c1.2.6 2 .3 2.7-.5l-1.7-1.6-1.2.6c-1-.5-2-1.6-2.5-2.6l.6-1.2z" fill="#fff"/></svg>
    <span>Office: 770-555-4821 &nbsp;|&nbsp; Cell: 770-555-3067</span>
  </div>
  <div class="contact contact-line">
    <span class="item">
      <svg viewBox="0 0 20 20" fill="none" stroke="#fff" stroke-width="1.3"><circle cx="10" cy="10" r="8"/><ellipse cx="10" cy="10" rx="3.5" ry="8"/><path d="M2 10h16M3.5 6h13M3.5 14h13"/></svg>
      <span>www.tkfenwick.example</span>
    </span>
    <span class="item">
      <svg viewBox="0 0 20 20" fill="none" stroke="#fff" stroke-width="1.4"><circle cx="10" cy="10" r="8.5"/><rect x="5.5" y="7" width="9" height="6.5"/><path d="M5.5 7l4.5 3.5 4.5-3.5"/></svg>
      <span>dale@tkfenwick.example</span>
    </span>
  </div>
  <div class="contact contact-address"><span>4700 West Harbor Boulevard, Suite #150, Roswell, GA 30076</span></div>
</section>

<section class="card card-back">
  <svg class="band" viewBox="0 0 821 470" preserveAspectRatio="none" aria-hidden="true">
    <path d="M0,428 Q410,348 821,428 L821,470 L0,470 Z" fill="var(--brand-green)"/>
    <path d="M0,424 Q410,342 821,424 Q410,348 0,428 Z" fill="var(--deep-green)"/>
  </svg>
  <div class="back-mark"></div>
  <div class="back-name">T.K. Fenwick</div>
  <div class="back-since">SINCE 1918</div>
  <div class="contact back-web">
    <svg viewBox="0 0 20 20" fill="none" stroke="#fff" stroke-width="1.3"><circle cx="10" cy="10" r="8"/><ellipse cx="10" cy="10" rx="3.5" ry="8"/><path d="M2 10h16M3.5 6h13M3.5 14h13"/></svg>
    <span>www.tkfenwick.example</span>
  </div>
</section>

</body>
</html>
```